business card deign

Logo needs the following on it.
1. attached logo
2. Tagline - "If it keeps a drink cold or the party going...we do it!"
3. Name- Dalton Pikes, Founder and CPO
4. Address - 412 E. Carver Avenue, Ste 2207, Tampa, FL. 33917
5. Phone - 555.318.4726

```html
<!DOCTYPE html>
<html lang="en">
<head>
<meta charset="utf-8">
<title>Frostbay Business Card</title>
<link href="https://fonts.googleapis.com/css2?family=Roboto:wght@400;500;700&display=swap" rel="stylesheet">
<style>
  :root {
    --stage: #222222;
    --card-dark: #111111;
    --card-light: #ffffff;
    --ink: #0d0d0d;
    --ink-soft: #2a2a2a;
    --paper: #ffffff;
    --rule: #333333;
  }
  * { box-sizing: border-box; margin: 0; padding: 0; }
  html, body {
    width: 1200px; height: 711px; overflow: hidden;
    background: var(--stage);
    font-family: "Roboto", Arial, sans-serif;
  }
  .stage {
    width: 1200px; height: 711px;
    display: flex; align-items: center; justify-content: center; gap: 40px;
  }
  .card {
    width: 540px; height: 309px; position: relative;
    border-radius: 4px;
    box-shadow: 0 14px 30px rgba(0,0,0,0.55);
  }
  .card--front {
    background: var(--card-dark);
    display: flex; align-items: center; justify-content: center;
  }
  .card--back { background: var(--card-light); color: var(--ink); }

  .brand { display: flex; align-items: center; gap: 12px; }
  .brand__dot { border-radius: 50%; flex: none; }
  .brand__name { font-weight: 700; letter-spacing: 0; line-height: 1; }
  .card--front .brand__dot { background: var(--paper); width: 22px; height: 22px; }
  .card--front .brand__name { color: var(--paper); font-size: 44px; }
  .card--back .brand {
    position: absolute; left: 30px; top: 120px; width: 210px;
    justify-content: center; gap: 9px;
  }
  .card--back .brand__dot { background: var(--ink); width: 15px; height: 15px; }
  .card--back .brand__name { color: var(--ink); font-size: 30px; }

  .divider {
    position: absolute; left: 262px; top: 52px;
    width: 1px; height: 170px; background: var(--rule);
  }
  .contact { position: absolute; left: 290px; top: 62px; }
  .contact__name { font-size: 26px; font-weight: 700; line-height: 1.1; }
  .contact__title { font-size: 14px; font-weight: 400; color: var(--ink-soft); margin-top: 4px; }
  .contact__list { list-style: none; margin-top: 24px; font-size: 13px; line-height: 1.45; }
  .contact__item { display: flex; gap: 8px; align-items: flex-start; }
  .contact__icon { width: 12px; height: 12px; margin-top: 3px; flex: none; }
  .tagline {
    position: absolute; left: 0; right: 0; bottom: 30px;
    text-align: center; font-size: 13.5px; font-weight: 500;
  }
</style>
</head>
<body>
<main class="stage">
  <section class="card card--front" aria-label="Card front">
    <div class="brand">
      <span class="brand__dot"></span>
      <span class="brand__name">Frostbay</span>
    </div>
  </section>

  <section class="card card--back" aria-label="Card back">
    <div class="brand">
      <span class="brand__dot"></span>
      <span class="brand__name">Frostbay</span>
    </div>
    <div class="divider"></div>
    <div class="contact">
      <h1 class="contact__name">Dalton Pikes</h1>
      <p class="contact__title">Founder and CPO</p>
      <ul class="contact__list">
        <li class="contact__item">
          <svg class="contact__icon" viewBox="0 0 24 24" aria-hidden="true"><path fill="#0d0d0d" d="M6.6 10.8a15.1 15.1 0 0 0 6.6 6.6l2.2-2.2a1 1 0 0 1 1-.25 11.4 11.4 0 0 0 3.6.57 1 1 0 0 1 1 1V20a1 1 0 0 1-1 1A17 17 0 0 1 3 4a1 1 0 0 1 1-1h3.5a1 1 0 0 1 1 1c0 1.25.2 2.45.57 3.57a1 1 0 0 1-.25 1z"/></svg>
          <span>555.318.4726</span>
        </li>
        <li class="contact__item">
          <svg class="contact__icon" viewBox="0 0 24 24" aria-hidden="true"><path fill="#0d0d0d" d="M12 2a7 7 0 0 0-7 7c0 5.2 7 13 7 13s7-7.8 7-13a7 7 0 0 0-7-7zm0 9.5A2.5 2.5 0 1 1 12 6.5a2.5 2.5 0 0 1 0 5z"/></svg>
          <span>412 E. Carver Avenue,<br>Ste 2207, Tampa, FL. 33917</span>
        </li>
      </ul>
    </div>
    <p class="tagline">If it keeps a drink cold or the party going...we do it!</p>
  </section>
</main>
</body>
</html>
```